Veldmark Supplies Business Card

Professional business card that stand out to our potential customers. Front and back with clean modern design

Industry/Entity Type

Oil and gas

Contact Information for Business Card

Name, address, website , office phone and cell number

Requirements
Must have
• Editable files for each employee

```html
<!DOCTYPE html>
<html lang="en">
<head>
<meta charset="utf-8">
<title>Veldmark Supplies Business Card</title>
<link href="https://fonts.googleapis.com/css2?family=Montserrat:wght@400;500;800&display=swap" rel="stylesheet">
<style>
  :root {
    --bg: #c4c4c4;
    --card-white: #ffffff;
    --card-black: #231f20;
    --brand-red: #ed1c24;
    --brand-cyan: #1aa9cf;
    --ink: #231f20;
    --emboss: #3a3637;
  }
  * { margin: 0; padding: 0; box-sizing: border-box; }
  html, body { width: 1200px; height: 815px; overflow: hidden; }
  body {
    background: var(--bg);
    font-family: "Montserrat", sans-serif;
    display: flex;
    align-items: center;
    justify-content: center;
    gap: 50px;
  }
  .card {
    position: relative;
    width: 525px;
    height: 300px;
    border-radius: 26px;
    overflow: hidden;
    box-shadow: 0 10px 28px rgba(0,0,0,0.25);
  }
  .card-front { background: var(--card-white); color: var(--ink); }
  .card-back {
    background: var(--card-black);
    display: flex;
    align-items: center;
    justify-content: center;
  }
  .corner-tab {
    position: absolute;
    top: 0; right: 0;
    width: 44px; height: 30px;
    background: var(--brand-red);
  }
  .person {
    position: absolute;
    top: 34px; right: 58px;
    text-align: right;
  }
  .person-name {
    font-weight: 800;
    font-size: 30px;
    letter-spacing: 0.5px;
    line-height: 1;
  }
  .person-name .first { color: var(--brand-red); }
  .person-name .last { color: var(--brand-cyan); }
  .person-role {
    font-size: 13px;
    font-weight: 500;
    margin-top: 6px;
  }
  .divider {
    position: absolute;
    left: 40px; right: 40px;
    top: 112px;
    height: 1.5px;
    background: var(--brand-cyan);
  }
  .location {
    position: absolute;
    top: 128px; right: 40px;
    display: flex;
    align-items: center;
    gap: 8px;
    font-size: 13px;
    font-weight: 500;
  }
  .brand {
    position: absolute;
    left: 40px; top: 152px;
    display: flex;
    align-items: center;
    gap: 12px;
  }
  .brand-square {
    width: 34px; height: 34px;
    background: var(--brand-red);
  }
  .brand-name {
    font-weight: 800;
    font-size: 22px;
    color: var(--brand-red);
    text-transform: uppercase;
    letter-spacing: 0.5px;
  }
  .contacts {
    position: absolute;
    left: 40px; bottom: 26px;
    list-style: none;
    font-size: 14px;
    line-height: 22px;
  }
  .contacts li { display: flex; align-items: center; gap: 10px; }
  .contacts svg { width: 13px; height: 13px; flex: none; }
  .back-brand {
    display: flex;
    align-items: center;
    gap: 16px;
  }
  .back-brand-square { width: 52px; height: 52px; background: var(--emboss); }
  .back-brand-name {
    font-weight: 800;
    font-size: 30px;
    color: var(--emboss);
    text-transform: uppercase;
    letter-spacing: 1px;
  }
</style>
</head>
<body>
  <section class="card card-front">
    <div class="corner-tab"></div>
    <div class="person">
      <p class="person-name"><span class="first">Daniel</span> <span class="last">Marsh</span></p>
      <p class="person-role">Manager</p>
    </div>
    <div class="divider"></div>
    <p class="location">Ho Chi Minh, Vietnam
      <svg width="12" height="14" viewBox="0 0 12 14" aria-hidden="true"><path d="M6 0a5 5 0 0 1 5 5c0 3.5-5 9-5 9S1 8.5 1 5a5 5 0 0 1 5-5z" fill="var(--brand-red)"/><circle cx="6" cy="5" r="2" fill="#fff"/></svg>
    </p>
    <div class="brand">
      <div class="brand-square"></div>
      <p class="brand-name">Veldmark Supplies</p>
    </div>
    <ul class="contacts">
      <li><svg viewBox="0 0 14 14" aria-hidden="true"><path d="M3 1l2.5 3-1.5 1.5a8 8 0 0 0 4.5 4.5L10 8.5l3 2.5-1.5 2C6 13 1 8 1 2.5z" fill="var(--brand-red)"/></svg>1-555-014-0187</li>
      <li><svg viewBox="0 0 14 14" aria-hidden="true"><rect x="1" y="3" width="12" height="8" fill="var(--brand-red)"/><path d="M1 3l6 5 6-5" stroke="#fff" fill="none"/></svg>dmarsh@northgridparts.vn</li>
      <li><svg viewBox="0 0 14 14" aria-hidden="true"><circle cx="7" cy="7" r="6" fill="none" stroke="var(--brand-red)" stroke-width="1.5"/><path d="M1 7h12M7 1c-3 3-3 9 0 12M7 1c3 3 3 9 0 12" stroke="var(--brand-red)" fill="none"/></svg>www.northgridparts.vn</li>
      <li><svg viewBox="0 0 14 14" aria-hidden="true"><circle cx="7" cy="7" r="6" fill="none" stroke="var(--brand-red)" stroke-width="1.5"/><path d="M1 7h12M7 1c-3 3-3 9 0 12M7 1c3 3 3 9 0 12" stroke="var(--brand-red)" fill="none"/></svg>www.northgridparts.com</li>
    </ul>
  </section>

  <section class="card card-back">
    <div class="back-brand">
      <div class="back-brand-square"></div>
      <p class="back-brand-name">Veldmark Supplies</p>
    </div>
  </section>
</body>
</html>
```